Flyer for customer acquisition.

Hello, We are a sportmanagement agency from Germany and we need information flyers for customer acquisition. It should be DinA4 and should have a modern but serious design. I have uploaded a information sheet, where you can find the text and the composition, the flyer should have. I also uploaded Pictures / Images, which you can use. Of course you can use other suitable images. If they are not free, I will buy them later. On the bottom of the flyer there has been the contact information. You will find them in the download section, too. If you have questions, just write me. If I forgot something, I will update the letter :) Thank you very much!
Ich brauche zusätzliche Tage um durchzusehen

```html
<!DOCTYPE html>
<html lang="de">
<head>
<meta charset="utf-8">
<title>NORVEX Nachwuchsförderung Flyer</title>
<link href="https://fonts.googleapis.com/css2?family=Oswald:wght@500&family=Raleway:wght@400;600;700&display=swap" rel="stylesheet">
<style>
  :root {
    --backdrop: #8d9295;
    --paper: #ffffff;
    --ink: #1a1a1a;
    --black: #0a0a0a;
    --blue: #1fa8d8;
    --blue-deep: #0f7fb0;
    --grey-band: #eceef0;
    --grass: #7cc43a;
  }
  * { box-sizing: border-box; margin: 0; padding: 0; }
  html, body { width: 974px; height: 1200px; overflow: hidden; background: var(--backdrop); }
  .flyer {
    position: absolute; left: 24px; top: 0; width: 926px; height: 1200px;
    background: var(--paper); overflow: hidden;
    font-family: "Raleway", sans-serif; color: var(--ink);
  }
  .abs { position: absolute; }
  .chess-visual {
    left: 62px; top: 12px; width: 305px; height: 114px;
    background: linear-gradient(180deg, #9fd65a, #5fa82a);
    border-radius: 40px 40px 6px 6px;
  }
  .header-shapes { left: 0; top: 0; width: 926px; height: 340px; }
  .title {
    left: 58px; top: 150px; color: #fff;
    font-family: "Oswald", sans-serif; font-weight: 500;
    font-size: 29px; line-height: 32px; letter-spacing: 0.3px;
  }
  .brand {
    left: 600px; top: 120px; width: 230px; text-align: center;
    color: #fff; font-weight: 700; font-size: 34px; letter-spacing: 1px;
    display: flex; align-items: center; justify-content: center; gap: 10px;
  }
  .brand .dot { width: 14px; height: 14px; border-radius: 50%; background: #fff; }
  .tagline {
    left: 57px; top: 251px; color: var(--blue);
    font-weight: 700; font-size: 20px; line-height: 22px;
  }
  .player-visual {
    left: 0; top: 318px; width: 342px; height: 750px;
    background: linear-gradient(180deg, #ececec 0%, #9a9a9a 35%, #c9e6f3 70%, #5ab8de 100%);
    border-bottom-left-radius: 110px;
  }
  .service { width: 222px; }
  .service .icon {
    width: 77px; height: 77px; border-radius: 50%; background: var(--blue);
    color: #fff; font-size: 10px; font-weight: 600; line-height: 12px;
    display: flex; align-items: center; justify-content: center; text-align: center;
    margin-bottom: 18px;
  }
  .service h2 { font-size: 16px; font-weight: 700; line-height: 19px; margin-bottom: 3px; }
  .service p { font-size: 13px; line-height: 16px; }
  .bottom-band { left: 0; top: 1068px; width: 926px; height: 132px; background: var(--black); }
  .footnotes {
    left: 55px; top: 1082px; width: 505px; text-align: center;
    color: #fff; font-size: 9.4px; line-height: 12.4px;
  }
  .contact-bar {
    left: 0; top: 1148px; width: 926px; height: 33px; background: var(--blue);
    color: #fff; font-size: 15px; line-height: 33px; padding-left: 35px;
    white-space: nowrap;
  }
  .team-visual {
    left: 600px; top: 966px; width: 324px; height: 234px;
    background: linear-gradient(180deg, #d8d8d8 0%, #3a3a3a 40%, #151515 100%);
    border-radius: 70px 70px 0 0;
  }
</style>
</head>
<body>
<main class="flyer">
  <div class="abs chess-visual" role="img" aria-label="Reihe grüner Schachfiguren aus Rasen"></div>

  <svg class="abs header-shapes" viewBox="0 0 926 340" aria-hidden="true">
    <defs>
      <linearGradient id="bannerBlue" x1="0" y1="0" x2="0" y2="1">
        <stop offset="0" stop-color="#26b3e3"/>
        <stop offset="1" stop-color="#1592c4"/>
      </linearGradient>
    </defs>
    <path d="M0 229 L0 330 L330 330 C380 330 400 258 470 258 L926 258 L926 229 Z" fill="var(--grey-band)"/>
    <path d="M0 330 L330 330 C380 330 400 258 470 258 L560 258" fill="none" stroke="#5a3a2a" stroke-width="1.2"/>
    <path d="M432 127 C470 110 470 45 540 38 L926 38 L926 266 L560 266 C500 266 500 150 432 127 Z" fill="url(#bannerBlue)"/>
    <path d="M0 137 L498 137 C520 137 525 229 545 229 L0 229 Z" fill="var(--black)"/>
  </svg>

  <h1 class="abs title">NORVEX NACHWUCHSFÖRDERUNG<br>UND -MANGEMENT</h1>
  <div class="abs brand"><span class="dot"></span>NORVEX</div>
  <p class="abs tagline">Wir begleiten dich auf<br>deinem Weg zum Profi</p>

  <div class="abs player-visual" role="img" aria-label="Illustration eines Fußballspielers von hinten mit Ball"></div>

  <section class="abs service" style="left:388px;top:322px">
    <div class="icon">ICON<br>WILL<br>COME<br>HERE</div>
    <h2>Karriereplanung</h2>
    <p>Wir haben deine Karriere im Blick! In enger Absprache mit deinen Eltern und dir leiten wir die richtigen Maßnahmen und Schritte ein, um dein Ziel „Profifußballer“ zu realisieren.</p>
  </section>
  <section class="abs service" style="left:631px;top:322px">
    <div class="icon">ICON<br>WILL<br>COME<br>HERE</div>
    <h2>Ständiger Ansprechpartner</h2>
    <p>Egal um welchen Themen es sich handelt, wir sind für dich da! Ein vertrauensvolles und freundschaftliches Verhältnis ist uns besonders wichtig.</p>
  </section>
  <section class="abs service" style="left:388px;top:539px">
    <div class="icon">ICON<br>WILL<br>COME<br>HERE</div>
    <h2>Rechtsberatung<br>/Vertragsrecht</h2>
    <p>Juristendeutsch und Kleingedrucktes? Kein Problem! Wir helfen dir den Durchblick zu behalten und holen immer das Beste für dich raus.</p>
  </section>
  <section class="abs service" style="left:631px;top:539px">
    <div class="icon">ICON<br>WILL<br>COME<br>HERE</div>
    <h2>Ausrüstung</h2>
    <p>Wir besorgen dir deine Ausrüstung! Unsere Beziehungen zu den großen Sportartikelherstellern ermöglichen den Abschluss von Ausrüsterverträgen*.</p>
  </section>
  <section class="abs service" style="left:388px;top:761px">
    <div class="icon">ICON<br>WILL<br>COME<br>HERE</div>
    <h2>Kooperationspartner/<br>Netzwerk</h2>
    <p>Ob Entscheidungsträger oder Experte, wir kennen die richtigen Leute. Zusätzlich bieten wir dir eine große Bandbreite an Leistungen, die du jederzeit in Anspruch nehmen kannst**.</p>
  </section>
  <section class="abs service" style="left:631px;top:761px">
    <div class="icon">ICON<br>WILL<br>COME<br>HERE</div>
    <h2>Vorsorge</h2>
    <p>Verletzungen gehören leider zum Fußball dazu. Wir sichern dich ab, indem wir eine private Zusatzkrankenversicherung für dich abschließen.</p>
  </section>

  <div class="abs bottom-band"></div>
  <p class="abs footnotes">*Die Entscheidung über das Zustandekommen eines Ausrüstervertrags obliegt dem jeweiligen Sportartikelhersteller. Ist ein Abschluss aktuell nicht möglich, erhältst du von uns 2x pro Saison neue Fußballschuhe sowie weitere Ausrüstungsgegenstände.<br>**Personal Training, Athletik-Training, Ernährungsberatung, Sportpsychologische Betreuung, uvm</p>
  <div class="abs contact-bar">Tel.: 0711/5550123 | E-Mail: info@norvex-sport.de | web: www.norvex-sport.de</div>

  <div class="abs team-visual" role="img" aria-label="Foto des dreiköpfigen Teams in dunklen Anzügen"></div>
</main>
</body>
</html>
```